Note/Card sent to show appreciation to partners who worked with us to improve local communities

I'd like a simple note/card designed for a wide audience. Originally, I called this a "Thanksgiving Card," but it's really just a card to be sent around Thanksgiving, not specifically celebrating the Thanksgiving holiday. We plan to send the card out just prior to Thanksgiving 2017 (Nov. 24, 2017). I work at a regulated electric utility, and we'd like to say thank you to the many stakeholders who we partner with throughout the year to support initiatives that help to improve our state and create opportunities for economic growth. I'm interested mostly in the design of the card, not the simple verbiage on the inside.
Target Market(s)
Customers, charitable foundations, nonprofits, advocacy groups, industry associations, friends

```html
<!DOCTYPE html>
<html lang="en">
<head>
<meta charset="utf-8">
<title>Thanks card</title>
<link rel="stylesheet" href="https://fonts.googleapis.com/css2?family=Caladea:wght@400;700&display=swap">
<style>
  :root {
    --orange: #f7941d;
    --cream: #fde3c2;
    --purple: #652d91;
    --white: #ffffff;
  }
  html, body {
    margin: 0;
    padding: 0;
    overflow: hidden;
    background: var(--orange);
  }
  .card {
    position: relative;
    width: 849px;
    height: 1200px;
    overflow: hidden;
    background: var(--orange);
    font-family: "Caladea", "Cambria", serif;
  }
  .sweep {
    position: absolute;
    inset: 0;
    width: 849px;
    height: 1200px;
  }
  .brand {
    position: absolute;
    left: 118px;
    top: 170px;
    display: flex;
    align-items: center;
    gap: 14px;
    color: var(--white);
    font-size: 46px;
    font-weight: 400;
    line-height: 1;
    margin: 0;
  }
  .brand-dot {
    width: 26px;
    height: 26px;
    border-radius: 50%;
    background: var(--white);
  }
  .message-panel {
    position: absolute;
    left: 88px;
    top: 366px;
    width: 671px;
    height: 603px;
    background: var(--purple);
    overflow: hidden;
  }
  .panel-sheen {
    position: absolute;
    inset: 0;
    width: 671px;
    height: 603px;
  }
  .headline {
    position: absolute;
    left: 0;
    right: 0;
    top: 136px;
    margin: 0;
    text-align: center;
    color: var(--white);
    font-size: 206px;
    font-weight: 400;
    line-height: 1;
    letter-spacing: -2px;
  }
</style>
</head>
<body>
<main class="card">
  <svg class="sweep" viewBox="0 0 849 1200" aria-hidden="true">
    <defs>
      <linearGradient id="sweep-fill" x1="0" y1="0" x2="1" y2="0.3">
        <stop offset="0" stop-color="#f7941d"/>
        <stop offset="0.45" stop-color="#fde3c2"/>
        <stop offset="1" stop-color="#f7941d"/>
      </linearGradient>
    </defs>
    <path d="M655,0 C660,420 470,860 0,1018 L0,1200 C540,980 790,560 849,0 Z" fill="url(#sweep-fill)"/>
  </svg>

  <p class="brand"><span class="brand-dot"></span>Brightline Power</p>

  <section class="message-panel">
    <svg class="panel-sheen" viewBox="88 366 671 603" aria-hidden="true">
      <defs>
        <linearGradient id="sheen-fill" x1="0" y1="0" x2="1" y2="0.3">
          <stop offset="0" stop-color="#ffffff" stop-opacity="0"/>
          <stop offset="0.5" stop-color="#ffffff" stop-opacity="0.28"/>
          <stop offset="1" stop-color="#ffffff" stop-opacity="0"/>
        </linearGradient>
      </defs>
      <path d="M655,0 C660,420 470,860 0,1018 L0,1200 C540,980 790,560 849,0 Z" fill="url(#sheen-fill)"/>
    </svg>
    <h1 class="headline">thanks</h1>
  </section>
</main>
</body>
</html>
```